Executive Business Card for Healthcare Company [Need Today]

I need a business card design for a healthcare company. The only branding the company has thus far is a logo. The cards will be utilized by company executives. The design I envision will be vibrant and appealing but with a corporate feel. They shouldn't be too casual or playful. I would like to complete this project TODAY if possible.

Target Market(s)

Healthcare vendors, other executives in healthcare and pharmaceuticals

Industry/Entity Type

Pharmaceutical

Contact Information for Business Card

See attachment

Font styles to use
Serif
Sans Serif

Colors

Designer to choose colors to be used in the design.

```html
<!DOCTYPE html>
<html lang="en">
<head>
<meta charset="utf-8">
<title>Corvina Therapeutics – Business Card</title>
<link rel="stylesheet" href="https://fonts.googleapis.com/css2?family=Roboto:wght@300;400;500;700&display=swap">
<style>
  :root {
    --teal: #34bfc8;
    --green: #5cbf92;
    --ink: #555a5e;
    --paper: #ffffff;
    --backdrop: #e9eaea;
  }
  * { margin: 0; padding: 0; box-sizing: border-box; }
  html, body { width: 1200px; height: 930px; overflow: hidden; }
  body {
    background: var(--backdrop);
    font-family: "Roboto", Arial, sans-serif;
    position: relative;
  }
  .card {
    position: absolute;
    width: 660px;
    height: 377px;
    border-radius: 18px;
    overflow: hidden;
    box-shadow: 0 6px 18px rgba(0,0,0,.18);
  }
  /* Front */
  .card-front { left: 110px; top: 55px; background: var(--teal); }
  .front-brand {
    position: absolute; inset: 0;
    display: flex; align-items: center; justify-content: center; gap: 22px;
  }
  .brand-mark {
    width: 96px; height: 96px; border-radius: 50%;
    border: 3px solid var(--paper);
  }
  .brand-name {
    color: var(--paper); font-weight: 300; font-size: 40px; line-height: 1.05;
  }
  /* Back */
  .card-back { left: 430px; top: 495px; background: var(--paper); }
  .back-brand {
    position: absolute; left: 38px; top: 46px;
    display: flex; align-items: center; gap: 14px;
  }
  .back-brand .brand-mark { width: 64px; height: 64px; border: 2px solid var(--green); }
  .back-brand .brand-name { color: var(--teal); font-size: 24px; }
  .identity {
    position: absolute; right: 38px; top: 42px; text-align: right;
  }
  .person-name { color: var(--teal); font-weight: 700; font-size: 32px; }
  .person-title { color: var(--ink); font-size: 15px; margin-top: 2px; }
  .rule-top {
    position: absolute; left: 300px; right: 38px; top: 118px;
    border-top: 1.5px solid var(--teal);
  }
  .address {
    position: absolute; right: 38px; top: 134px; text-align: right;
    color: var(--ink); font-size: 15px; line-height: 1.35;
  }
  .address .company { color: var(--teal); font-weight: 500; font-size: 16px; }
  .rule-bottom {
    position: absolute; left: 38px; width: 300px; top: 214px;
    border-top: 1.5px solid var(--teal);
  }
  .contacts {
    position: absolute; left: 42px; top: 232px; list-style: none;
    color: var(--ink); font-size: 16px; line-height: 1.5;
  }
  .contacts li { display: flex; align-items: center; gap: 10px; }
  .contacts svg { width: 14px; height: 14px; flex: none; }
  .base-band { position: absolute; left: 0; bottom: 0; width: 660px; height: 120px; }
</style>
</head>
<body>
  <section class="card card-front">
    <div class="front-brand">
      <span class="brand-mark"></span>
      <span class="brand-name">corvina<br>therapeutics</span>
    </div>
  </section>

  <section class="card card-back">
    <div class="back-brand">
      <span class="brand-mark"></span>
      <span class="brand-name">corvina<br>therapeutics</span>
    </div>

    <div class="identity">
      <div class="person-name">Daniel Marsh</div>
      <div class="person-title">Senior Director of Marketing</div>
    </div>
    <div class="rule-top"></div>
    <div class="address">
      <div class="company">Corvina Therapeutics, LLC</div>
      <div>418 W Harmon Street</div>
      <div>Fairview, GA 30799</div>
    </div>

    <div class="rule-bottom"></div>
    <ul class="contacts">
      <li><svg viewBox="0 0 14 14"><path d="M3 1l2 3-1.5 1.5c.8 1.8 2.2 3.2 4 4L9 8l3 2-1 2.5C6 12 2 8 1.5 3z" fill="var(--teal)"/></svg>555-014-2276</li>
      <li><svg viewBox="0 0 14 14"><rect x="3.5" y="1" width="7" height="12" rx="1.5" fill="none" stroke="var(--teal)" stroke-width="1.5"/><circle cx="7" cy="10.5" r=".9" fill="var(--teal)"/></svg>555-019-4830</li>
      <li><svg viewBox="0 0 14 14"><rect x="1" y="3" width="12" height="8" fill="none" stroke="var(--teal)" stroke-width="1.4"/><path d="M1 3l6 5 6-5" fill="none" stroke="var(--teal)" stroke-width="1.4"/></svg>dmarsh@corvinarx.com</li>
    </ul>

    <svg class="base-band" viewBox="0 0 660 120" preserveAspectRatio="none" aria-hidden="true">
      <path d="M0 104 L380 104 C410 104 420 70 450 66 L660 66 L660 120 L0 120 Z" fill="var(--teal)"/>
      <path d="M0 96 L376 96 L372 101 L0 101 Z" fill="var(--green)"/>
    </svg>
  </section>
</body>
</html>
```